Printed Circuit Board Company Web Site Design - Please see new file 82012 web design

We are a printed circuit board manufacturer. Need a company professional web site to allow our potential customers to know more about our background, capability and our products. The web site will contain three languages, which are Chinese, English and Japanese. Our audience are mainly electronic companies that procure printed circuit boards. I have a word document that have all the required text in all three languages. The final design should communicate the impression that we embrace quality, trustworthiness and long term partnership business principles.
We should have sections that allow us to post pictures of our facilities.
I have added the three files in three different languages.
Some of the information is below:
Background
RDV Harbourline Limited (RDV) was set up in Hong Kong in 2007 by two Hong Kong entrepreneurs, Mr. Tak Wong and Mr. Lok Fai. We acquired the single sided printed circuit board factory located in Dongguan City, Guangdong Province, China, from Tovand Corporation of the U.S. in 2007. In addition to RDV, Mr. Wong and Mr. Fai also own Halberd Technology Company Limited, a semiconductor company based in Hong Kong since 1997 with a total investment of over US$100 million. Halberd is engaged in the manufacturing of flexible substrates and MEMS assembly business.
RDV has been awarded TS 16949 and ISO14000 certificates since 2009 and 2004 respectively.
Business Principles
RDV Harbourline Limited strives to be a professional top notched printed circuit board supplier. We embrace four “EXCELLENCE” principles, namely, excellence in quality, excellence in prices, excellence in services and excellence in on time delivery.
We approach each customer with a long-term partnership view that delivers the lowest ownership costs and highest total values to our customers. We customize quotations and solutions in order to allow our customers to win more businesses. We believe by thinking from our customers’ points of view we will be able to create a WIN-WIN relationship.
Customers
Due to our excellent quality, services and production systems, RDV Harbourline Limited manage to service a number of large Japanese and US customers, which include:
Technical capability overview
Below is an overview of our current capability:
Target Market(s)
Electronic companies buyers
Industry/Entity Type
Business
Requirements
Must have
- Capability description
Should not have
- no cartoon

```html
<!DOCTYPE html>
<html lang="en">
<head>
<meta charset="utf-8">
<title>RDV Harbourline Limited</title>
<link href="https://fonts.googleapis.com/css2?family=Source+Sans+3:wght@400;600;700&display=swap" rel="stylesheet">
<style>
:root{
  --sky-top:#f4f7f9;
  --sky-bottom:#c9dbe5;
  --nav:#6a96ad;
  --nav-dark:#587f94;
  --brand:#1f8a5a;
  --ink:#1b1b1b;
  --button:#6b93a8;
  --footer:#658fa3;
  --white:#ffffff;
  --line:#d9d9d9;
}
*{box-sizing:border-box;margin:0;padding:0}
html,body{width:1200px;height:1149px;overflow:hidden}
body{position:relative;background:var(--white);font-family:"Source Sans 3",sans-serif;color:var(--ink)}
.masthead{position:absolute;left:0;top:0;width:1200px;height:480px;background:linear-gradient(var(--sky-top),var(--sky-bottom))}
.brand{position:absolute;left:166px;top:34px;display:flex;align-items:center;gap:10px;font-size:30px;font-weight:700;color:var(--brand);letter-spacing:.5px}
.brand-mark{width:22px;height:22px;background:var(--brand)}
.search{position:absolute;left:785px;top:36px;width:249px;height:37px;background:var(--nav);border-radius:3px;padding:7px 9px}
.search-field{height:22px;background:var(--white);border-radius:2px;font-size:12px;color:#555;padding:3px 10px;display:flex;justify-content:space-between;align-items:center}
.main-nav{position:absolute;left:162px;top:113px;width:874px;height:28px;display:flex;background:linear-gradient(#7ea8bd,var(--nav-dark));border-radius:3px;box-shadow:0 3px 5px rgba(0,0,0,.2)}
.main-nav a{color:var(--white);text-decoration:none;font-size:12px;display:flex;align-items:center;justify-content:center;border-right:1px solid #4f7487}
.main-nav a:last-child{border-right:0}
.slider{position:absolute;left:164px;top:154px;width:872px;height:307px;background:linear-gradient(100deg,#3d6b4a 0%,#c9cccb 30%,#e6e7e5 55%,#9aa7a7 80%,#5d7070 100%);border-radius:3px}
.slider-dots{position:absolute;left:540px;top:452px;display:flex;gap:6px}
.slider-dots span{width:15px;height:15px;background:var(--white);border:1px solid #999}
.slider-dots .active{background:radial-gradient(#1a8fd6 35%,var(--white) 40%)}
h2{font-size:19px;font-weight:400;text-decoration:underline;text-underline-offset:3px}
.about{position:absolute;left:162px;top:504px;width:540px}
.about p{font-size:12px;line-height:18.5px;margin-top:9px}
.about p+p{margin-top:17px}
.btn{display:inline-block;background:var(--button);color:var(--white);font-size:12px;padding:5px 10px}
.about .btn{margin-top:10px}
.services{position:absolute;left:162px;top:751px;width:420px}
.service-list{list-style:none;display:grid;grid-template-columns:226px 200px;row-gap:13px;margin-top:16px}
.service-list li{display:flex;align-items:center;gap:12px;font-size:12px;text-decoration:underline}
.news{position:absolute;left:753px;top:504px}
.news-box{position:absolute;left:-1px;top:36px;width:277px;height:369px;border:1px solid var(--line);padding:12px 10px}
.news-item{display:flex;gap:13px;height:117px}
.news-photo{width:96px;height:97px;flex:none}
.news-item h3{font-size:12.5px;font-weight:400;display:flex;align-items:center;gap:7px;margin-top:0}
.news-item p{font-size:11px;line-height:14px;margin:6px 0 8px}
.site-footer{position:absolute;left:0;top:927px;width:1200px;height:222px;background:var(--footer);color:var(--white);font-size:10.5px;line-height:14px}
.office{position:absolute;left:159px}
.office h4{font-size:11px;font-weight:600;text-decoration:underline;margin-bottom:8px}
.follow{position:absolute;right:177px;top:35px;text-align:right}
.social{display:flex;gap:6px;margin-top:12px;justify-content:flex-end}
.social span{width:24px;height:24px;border-radius:3px;background:#3b6fb0}
.footer-links{position:absolute;right:177px;top:148px;text-align:right}
</style>
</head>
<body>
<header class="masthead">
  <div class="brand"><span class="brand-mark"></span>RDV Harbourline</div>
  <div class="search"><div class="search-field">Search
    <svg width="13" height="13" viewBox="0 0 13 13"><circle cx="5" cy="5" r="3.8" fill="none" stroke="#888" stroke-width="1.3"/><line x1="8" y1="8" x2="12" y2="12" stroke="#888" stroke-width="1.6"/></svg></div></div>
  <nav class="main-nav">
    <a href="#" style="width:126px">HOME</a><a href="#" style="width:119px">ABOUT US</a><a href="#" style="width:111px">SERVICES</a><a href="#" style="width:114px">PRODUCTS</a><a href="#" style="width:126px">NEWS</a><a href="#" style="width:136px">BLOG</a><a href="#" style="width:142px">CONTACT US</a>
  </nav>
  <div class="slider" role="img" aria-label="Factory worker feeding printed circuit boards through a production machine"></div>
  <div class="slider-dots"><span></span><span></span><span class="active"></span><span></span><span></span></div>
</header>

<section class="about">
  <h2>RDV Harbourline Limited</h2>
  <p>RDV Harbourline Limited (RDV) was set up in Hong Kong in 2007 by two Hong Kong entrepreneurs, Mr. Tak Wong and Mr. Lok Fai. We acquired the single sided printed circuit board factory located in Dongguan City, Guangdong Province, China, from Tovand Corporation of the U.S. in 2007. In addition to RDV, Mr. Wong and Mr. Fai also own Halberd Technology Company Limited, a semiconductor company based in Hong Kong since 1997 with a total investment of over US$100 million. Halberd is engaged in the manufacturing of flexible substrates and MEMS assembly business.</p>
  <p>RDV has been awarded TS 16949 and ISO14000 certificates since 2009 and 2004 respectively.</p>
  <a class="btn" href="#">More info</a>
</section>

<section class="services">
  <h2>Our Main Services</h2>
  <ul class="service-list">
    <li><svg width="15" height="16"><rect x="1" y="1" width="10" height="13" fill="#fff" stroke="#999"/><circle cx="11" cy="12" r="3.5" fill="#2a86c5"/></svg>Raw Materials</li>
    <li><svg width="15" height="16"><rect x="1" y="1" width="10" height="13" fill="#fff" stroke="#999"/><circle cx="11" cy="12" r="3.5" fill="#2a86c5"/></svg>V-Cut</li>
    <li><svg width="15" height="16"><rect x="1" y="1" width="10" height="13" fill="#fff" stroke="#999"/><circle cx="11" cy="12" r="3.5" fill="#2a86c5"/></svg>Plating</li>
    <li><svg width="15" height="16"><rect x="1" y="1" width="10" height="13" fill="#fff" stroke="#999"/><circle cx="11" cy="12" r="3.5" fill="#2a86c5"/></svg>Surface Finishing</li>
    <li><svg width="15" height="16"><rect x="1" y="1" width="10" height="13" fill="#fff" stroke="#999"/><circle cx="11" cy="12" r="3.5" fill="#2a86c5"/></svg>Printing Processes</li>
    <li><svg width="15" height="16"><rect x="1" y="1" width="10" height="13" fill="#fff" stroke="#999"/><circle cx="11" cy="12" r="3.5" fill="#2a86c5"/></svg>Specification for carbon</li>
    <li><svg width="15" height="16"><rect x="1" y="1" width="10" height="13" fill="#fff" stroke="#999"/><circle cx="11" cy="12" r="3.5" fill="#2a86c5"/></svg>Punching And CNC Process</li>
    <li><svg width="15" height="16"><rect x="1" y="1" width="10" height="13" fill="#fff" stroke="#999"/><circle cx="11" cy="12" r="3.5" fill="#2a86c5"/></svg>Plating</li>
  </ul>
</section>

<section class="news">
  <h2>News</h2>
  <div class="news-box">
    <article class="news-item">
      <div class="news-photo" role="img" aria-label="Portrait of a smiling senior man" style="background:linear-gradient(#e4e6e8,#b9a79a)"></div>
      <div><h3><svg width="14" height="14"><rect x="1" y="1" width="11" height="12" fill="#fff" stroke="#999"/></svg>Why Choose Us?</h3>
      <p>RDV Harbourline Limited strives to be a professional top notched printed</p><a class="btn" href="#">More info</a></div>
    </article>
    <article class="news-item">
      <div class="news-photo" role="img" aria-label="Portrait of a smiling young woman" style="background:linear-gradient(#f0f0f0,#9c7a62)"></div>
      <div><h3><svg width="14" height="14"><rect x="1" y="1" width="11" height="12" fill="#fff" stroke="#999"/></svg>Our Experience</h3>
      <p>RDV Harbourline Limited strives to be a professional top notched printed</p><a class="btn" href="#">More info</a></div>
    </article>
    <article class="news-item">
      <div class="news-photo" role="img" aria-label="Portrait of a smiling woman resting her chin on her hand" style="background:linear-gradient(#f2f2f2,#c9a58e)"></div>
      <div><h3><svg width="14" height="14"><rect x="1" y="1" width="11" height="12" fill="#fff" stroke="#999"/></svg>Our Experience</h3>
      <p>RDV Harbourline Limited strives to be a professional top notched printed</p><a class="btn" href="#">More info</a></div>
    </article>
  </div>
</section>

<footer class="site-footer">
  <div class="office" style="top:34px">
    <h4>Hong Kong Business Office</h4>
    RDV Harbourline Limited, 28/F Kestrel Plaza, 17 Marlow Road<br>Harbour Point, HONG KONG, Telephone: (852)30456218<br>Fax: (852)30456290, Email: sales@rdvharbourline.com
  </div>
  <div class="office" style="top:127px">
    <h4>China Factory</h4>
    RDV Harbourline (Dongguan) Limited<br>9 Linfeng East 4 Road, 52 Industrial District<br>Qiaowei Town, Dongguan, Guangdong Province, China 523840<br>Telephone: (86)769-86204417, Fax: (86)769-86204490
  </div>
  <div class="follow">Follow Us On
    <div class="social"><span style="background:#3b5e9c"></span><span style="background:#3aa2d8"></span><span style="background:#2a6ea8"></span><span style="background:#ea8a1e"></span></div>
  </div>
  <div class="footer-links">Home &nbsp;|&nbsp; About Us &nbsp;|&nbsp; Services &nbsp;|&nbsp; Products &nbsp;|&nbsp; News &nbsp;|&nbsp; Blog &nbsp;|&nbsp; Contact Us<br><span style="line-height:20px">Copyrights @ 2012 All Rights Reserved</span></div>
</footer>
</body>
</html>
```